Coastline Premier Retreats Business Card Design

Design a business card for Coastline Premier Retreats. Look at the website for colors and reference. Card should have logo, name, title, office number, mobile number, email, URL and a tagline like, "Luxury Hotel & Resort Email Marketing" (This might change).

https://www.coastlinepremierretreats.example

The rest I will leave up to your imagination.

Contact Information for Business Card

Logo, name, title, office number, mobile number, email, URL and a tagline like, "Luxury Hotel & Resort Email Marketing" (This might change).

```html
<!DOCTYPE html>
<html lang="en">
<head>
<meta charset="UTF-8">
<title>Coastline Premier Retreats — Business Card</title>
<link href="https://fonts.googleapis.com/css2?family=Montserrat:wght@400;500;700;800&display=swap" rel="stylesheet">
<style>
  :root {
    --backdrop: #232325;
    --card: #2c2c30;
    --accent: #f47a20;
    --ink: #ffffff;
    --ink-soft: #e6e6e6;
  }
  * { margin: 0; padding: 0; box-sizing: border-box; }
  html, body { width: 1200px; height: 900px; overflow: hidden; }
  body {
    background: var(--backdrop);
    font-family: "Montserrat", Arial, sans-serif;
    color: var(--ink);
    position: relative;
  }
  .card {
    position: absolute;
    width: 540px;
    height: 310px;
    background: var(--card);
    border-radius: 16px;
    border-bottom: 4px solid var(--accent);
    box-shadow: 0 18px 40px rgba(0,0,0,0.45);
    overflow: hidden;
  }
  .card--front { left: 90px; top: 100px; }
  .card--back { left: 570px; top: 470px; }

  .brand {
    display: flex;
    align-items: center;
    gap: 12px;
    color: var(--ink);
    font-weight: 800;
    text-transform: uppercase;
    letter-spacing: 0.04em;
    line-height: 1.05;
  }
  .brand__mark {
    width: 14px; height: 14px;
    background: var(--accent);
    flex: none;
  }
  .card--front .brand {
    position: absolute;
    left: 50%; top: 50%;
    transform: translate(-50%, -50%);
    font-size: 30px;
    width: 400px;
  }
  .card--back .brand {
    position: absolute;
    left: 34px; top: 112px;
    font-size: 17px;
    width: 190px;
  }
  .card--back .brand__mark { width: 10px; height: 10px; }

  .contact {
    position: absolute;
    left: 250px; top: 34px;
    padding-left: 18px;
    border-left: 2px solid var(--accent);
    height: 196px;
  }
  .contact__name {
    color: var(--accent);
    font-weight: 700;
    font-size: 19px;
  }
  .contact__title {
    font-size: 11px;
    color: var(--ink-soft);
    margin-bottom: 12px;
  }
  .contact__address {
    font-size: 11px;
    line-height: 1.45;
    color: var(--ink-soft);
    margin-bottom: 8px;
    font-style: normal;
  }
  .contact__list { list-style: none; }
  .contact__item {
    display: flex;
    align-items: center;
    gap: 10px;
    font-size: 11px;
    color: var(--ink-soft);
    line-height: 1.9;
    white-space: nowrap;
  }
  .contact__icon { width: 12px; height: 12px; fill: var(--accent); flex: none; }

  .tagline {
    position: absolute;
    right: 34px; bottom: 26px;
    font-size: 13px;
    font-weight: 500;
    color: var(--ink);
  }
</style>
</head>
<body>

<section class="card card--front" aria-label="Card front">
  <div class="brand"><span class="brand__mark"></span><span>Coastline Premier Retreats</span></div>
</section>

<section class="card card--back" aria-label="Card back">
  <div class="brand"><span class="brand__mark"></span><span>Coastline Premier Retreats</span></div>

  <div class="contact">
    <p class="contact__name">Daniel Harrow</p>
    <p class="contact__title">Owner</p>
    <address class="contact__address">145 Harbor Way, Suite 210<br>Bayview, CA 90210</address>
    <ul class="contact__list">
      <li class="contact__item">
        <svg class="contact__icon" viewBox="0 0 24 24"><path d="M6.6 10.8a15 15 0 0 0 6.6 6.6l2.2-2.2a1 1 0 0 1 1-.25 11.4 11.4 0 0 0 3.6.6 1 1 0 0 1 1 1V20a1 1 0 0 1-1 1A17 17 0 0 1 3 4a1 1 0 0 1 1-1h3.5a1 1 0 0 1 1 1c0 1.25.2 2.45.6 3.6a1 1 0 0 1-.25 1z"/></svg>
        555.014.2380 x 204
      </li>
      <li class="contact__item">
        <svg class="contact__icon" viewBox="0 0 24 24"><path d="M7 1h10a2 2 0 0 1 2 2v18a2 2 0 0 1-2 2H7a2 2 0 0 1-2-2V3a2 2 0 0 1 2-2zm0 3v14h10V4zm5 15.5a1 1 0 1 0 0 2 1 1 0 0 0 0-2z"/></svg>
        555.019.4471
      </li>
      <li class="contact__item">
        <svg class="contact__icon" viewBox="0 0 24 24"><path d="M2 5h20v14H2zm2 2v.5l8 5 8-5V7l-8 5z"/></svg>
        info@coastlinepremierretreats.example
      </li>
      <li class="contact__item">
        <svg class="contact__icon" viewBox="0 0 24 24"><path d="M12 2a10 10 0 1 0 0 20 10 10 0 0 0 0-20zm0 2c1 0 2.3 2 2.8 5H9.2C9.7 6 11 4 12 4zM4.3 11h3.8a18 18 0 0 0 0 2H4.3a8 8 0 0 1 0-2zm5 0h5.4a16 16 0 0 1 0 2H9.3a16 16 0 0 1 0-2zm6.6 0h3.8a8 8 0 0 1 0 2h-3.8a18 18 0 0 0 0-2zM9.2 15h5.6c-.5 3-1.8 5-2.8 5s-2.3-2-2.8-5z"/></svg>
        www.coastlinepremierretreats.example
      </li>
    </ul>
  </div>

  <p class="tagline">Luxury Hotel &amp; Resort Email Marketing</p>
</section>

</body>
</html>
```